Oil and Gas Exploration and Production company needs a business card design

We need a business card design using our logo and colors in the logo. We want a mainstream design.

```html
<!DOCTYPE html>
<html lang="en">
<head>
<meta charset="utf-8">
<title>Terrano Oil &amp; Gas — Business Card</title>
<link rel="stylesheet" href="https://fonts.googleapis.com/css2?family=Lato:wght@400;700;900&display=swap">
<style>
  :root {
    --bg: #2b2b2b;
    --ink: #111111;
    --paper: #ffffff;
    --gold: #c99a2e;
    --text: #333333;
  }
  html, body {
    margin: 0;
    padding: 0;
    width: 1200px;
    height: 960px;
    overflow: hidden;
    background: var(--bg);
    font-family: "Lato", sans-serif;
  }
  .stage {
    position: relative;
    width: 1200px;
    height: 960px;
  }
  .card {
    position: absolute;
    left: 250px;
    width: 700px;
    height: 400px;
    box-sizing: border-box;
    overflow: hidden;
    box-shadow: 0 10px 30px rgba(0,0,0,0.45);
  }
  .card-back {
    top: 50px;
    background: var(--ink);
    display: flex;
    align-items: center;
    justify-content: center;
  }
  .card-front {
    top: 510px;
    background: var(--paper);
  }
  .brand {
    display: flex;
    align-items: center;
    gap: 12px;
  }
  .brand-dot {
    border-radius: 50%;
    background: var(--gold);
    flex: none;
  }
  .brand-name {
    font-weight: 900;
    letter-spacing: 0.5px;
    white-space: nowrap;
  }
  .card-back .brand-dot { width: 44px; height: 44px; }
  .card-back .brand-name { color: var(--paper); font-size: 46px; }

  .card-front .brand {
    position: absolute;
    top: 58px;
    right: 48px;
  }
  .card-front .brand-dot { width: 30px; height: 30px; }
  .card-front .brand-name { color: var(--ink); font-size: 32px; }

  .person {
    position: absolute;
    left: 48px;
    top: 128px;
  }
  .person-name {
    margin: 0;
    color: var(--gold);
    font-weight: 700;
    font-size: 28px;
    line-height: 1.1;
  }
  .person-role {
    margin: 2px 0 0;
    color: var(--text);
    font-size: 18px;
  }
  .divider {
    position: absolute;
    left: 48px;
    right: 70px;
    top: 205px;
    height: 2px;
    background: var(--gold);
  }
  .contacts {
    position: absolute;
    left: 48px;
    top: 222px;
    margin: 0;
    padding: 0;
    list-style: none;
    color: var(--text);
    font-size: 15px;
  }
  .contacts li {
    display: flex;
    align-items: center;
    gap: 10px;
    height: 23px;
  }
  .contacts svg {
    width: 14px;
    height: 14px;
    fill: var(--gold);
    flex: none;
  }
  .address {
    position: absolute;
    right: 70px;
    top: 300px;
    margin: 0;
    text-align: right;
    color: var(--text);
    font-size: 16px;
    font-style: normal;
    line-height: 1.4;
  }
  .band {
    position: absolute;
    left: 0;
    bottom: 0;
    width: 700px;
    height: 18px;
  }
</style>
</head>
<body>
<main class="stage">

  <section class="card card-back" aria-label="Card back">
    <div class="brand">
      <span class="brand-dot"></span>
      <span class="brand-name">Terrano Oil &amp; Gas</span>
    </div>
  </section>

  <section class="card card-front" aria-label="Card front">
    <div class="brand">
      <span class="brand-dot"></span>
      <span class="brand-name">Terrano Oil &amp; Gas</span>
    </div>

    <div class="person">
      <h1 class="person-name">Daniel Hart</h1>
      <p class="person-role">President</p>
    </div>

    <div class="divider"></div>

    <ul class="contacts">
      <li>
        <svg viewBox="0 0 16 16" aria-hidden="true"><path d="M3.5 1l2.5 3-1.5 1.8c.9 2 2.6 3.7 4.7 4.7L11 9l3 2.5-1.6 2.8C7 14 2 9 1.5 3.2z"/></svg>
        555 210 4480
      </li>
      <li>
        <svg viewBox="0 0 16 16" aria-hidden="true"><path d="M4.5 1h7v14h-7zM6 2.5v9.5h4V2.5zM7.3 13h1.4v1H7.3z" fill-rule="evenodd"/></svg>
        555 318 2275
      </li>
      <li>
        <svg viewBox="0 0 16 16" aria-hidden="true"><path d="M1 3.5h14v1L8 9 1 4.5zM1 6l7 4.5L15 6v6.5H1z"/></svg>
        hello@terranoenergy.net
      </li>
      <li>
        <svg viewBox="0 0 16 16" aria-hidden="true"><path d="M8 1a7 7 0 100 14A7 7 0 008 1zm0 1.5c.8 0 1.7 1.6 2 4H6c.3-2.4 1.2-4 2-4zM2.6 6.5h2c-.1.5-.1 1-.1 1.5s0 1 .1 1.5h-2a5.5 5.5 0 010-3zm3.4 3h4c-.3 2.4-1.2 4-2 4s-1.7-1.6-2-4zm5.4 0c.1-.5.1-1 .1-1.5s0-1-.1-1.5h2a5.5 5.5 0 010 3z"/></svg>
        www.terranoenergy.net
      </li>
    </ul>

    <address class="address">Level 5, 27 Harbour Road<br>Eastport, WA 6100</address>

    <svg class="band" viewBox="0 0 700 18" preserveAspectRatio="none" aria-hidden="true">
      <polygon points="0,0 330,0 342,18 0,18" fill="var(--ink)"/>
      <polygon points="338,0 700,0 700,18 350,18" fill="var(--gold)"/>
    </svg>
  </section>

</main>
</body>
</html>
```